Suchen ansprechendes & seriöses Urkunden/Zertifikat Design für Webseite & Druck
Zielgruppe
Auf unserer Webseite http://wacker-im-alter.de können sich Unternehmen, Institutionen und Vereine ihre Seniorenfreundlichkeit durch ein Zertifikat bestätigen und zertifizieren lassen.
Unsere Kundengruppen: Hotel – Gastronomie – Wellness – Reisen und Touristik – Touristikregionen – Seniorenshop – Onlineshop – Unternehmen als Dienstleister – Medizin und Health-Service – Apotheke – Altenheim – Pflegeheim – Seniorenheim – Vereine – Seniorenservice – Zahnärzte – Fitnessstudio – Sportstudio – Physiotherapie – Sportverein – Golfclub – und viele weitere seniorenfreundliche Institutionen.
Aufgabenstellung
Auftrag- Ausschreibung:
- Erstellung eines Design:
- Urkunde für Webseite wacker-im-alter.de - Das Zertifikat "Wacker im Alter“
Funktion:
Kunde erkennt das Zertifikat - Logo auf einer Webseite und Klickt auf dieses.
Er wird weitergeleitet auf eine Unterseite, worin die Richtlinien und die Urkunde sichtbar wird.
Zielgruppe:
- Unternehmen, welche das Zertifikat auf Ihre Webseite setzen. Die Urkunde gibt Auskunft, dass der Dienstleister einen besonderen Service für Senioren ausübt. Die Urkunde ist sichtbar auf der Webseite, indem das Logo angeklickt wird. Die Urkunde gibt es ebenfalls als Download, damit der Kunde diese in seinen Geschäftsräumen aufhängen kann oder diese in seinen Werbeunterlagen präsentieren kann.
- Verbraucher sollen beeindruckt sein, von der Urkunde, welches Vertrauen ausstrahlt, aber auch Seriosität
Folgende Ausstrahlung soll die Urkunde haben:
- Soll Mitbewerber des Zertifikatsinhaber beeindrucken und das Verlangen aufzeigen, sich ebenfalls zertifizieren zu lassen ( ca: 70% der Kunden sind Mitbewerber … ). Nach dem Motto "Das Logo ist super und edel, das muss ich auch haben!"
- Der Kunde als Verbraucher soll Vertrauen gewinnen, die Daten sollen gut sichtbar sein, aber nicht verkitscht wie eine Urkunde bei einer Kaffeefahrt. Der Verbraucher geht auf das Zertifikat und kommt zur Urkunde, deshalb soll die Farbe, und Darstellung, Seriosität des Unternehmens ausstrahlen.
Sonstiges
- Die Urkunde soll dem neuen Design unserer Seite (zu sehen unter: http://gutsiegel-pruefung.de) angepasst sein.
- Vor Auftragsendvergabe erhalten Sie noch ein telefonisches Briefing über unsere Erfahrungswerte
Link zur bestehenden alten Webseite (Altes Design): http://wacker-im-alter.de
Info Verbraucher: http://www.wacker-im-alter.de/verbraucher/
Info zum Zertifikat: http://www.wacker-im-al..

```html
<!DOCTYPE html>
<html lang="de">
<head>
<meta charset="utf-8">
<title>Zertifikat – Wacker im Alter</title>
<link rel="stylesheet" href="https://fonts.googleapis.com/css2?family=Josefin+Sans:wght@200;300&family=Raleway:wght@400;600;700&display=swap">
<style>
  :root {
    --paper-light: #fbf8f3;
    --paper-mid: #efe7dc;
    --paper-edge: #e3d6c4;
    --gold: #a88d67;
    --gold-dark: #8a7152;
    --gold-soft: #cdbda5;
    --label: #6e5a43;
    --ink: #3a3430;
    --title: #4f4439;
  }
  * { margin: 0; padding: 0; box-sizing: border-box; }
  html, body { width: 850px; height: 1200px; overflow: hidden; background: var(--paper-light); }
  .certificate {
    position: relative;
    width: 850px; height: 1200px;
    background: radial-gradient(ellipse at 50% 45%, var(--paper-light) 0%, var(--paper-mid) 70%, var(--paper-edge) 100%);
    font-family: "Raleway", sans-serif;
    overflow: hidden;
  }
  .frame { position: absolute; inset: 0; }
  .emblem-backdrop {
    position: absolute; left: 150px; top: 300px; width: 550px; height: 780px;
    border-radius: 50% 50% 45% 45%;
    background: radial-gradient(ellipse at 50% 50%, rgba(205,189,165,0.28) 0%, rgba(205,189,165,0.12) 55%, rgba(205,189,165,0) 75%);
  }
  .wreath-backdrop {
    position: absolute; left: 255px; top: 90px; width: 340px; height: 280px;
    border-radius: 50%;
    background: radial-gradient(ellipse at 50% 50%, rgba(205,189,165,0.25) 0%, rgba(205,189,165,0) 70%);
  }
  .title {
    position: absolute; top: 105px; left: 0; width: 850px;
    text-align: center;
    font-family: "Josefin Sans", sans-serif;
    font-weight: 200;
    font-size: 122px;
    letter-spacing: 4px;
    line-height: 1;
    color: var(--title);
  }
  .ribbon { position: absolute; left: 160px; top: 225px; width: 530px; height: 130px; }
  .ribbon-text {
    font-family: "Raleway", sans-serif; font-weight: 400; font-size: 33px;
    fill: #ffffff; letter-spacing: 1px;
  }
  .details { position: absolute; left: 0; top: 410px; width: 850px; }
  .row { position: absolute; left: 0; display: flex; width: 850px; }
  .label {
    width: 350px; text-align: right; padding-right: 10px;
    font-weight: 600; font-size: 22px; line-height: 26px; color: var(--label);
  }
  .value { font-size: 22px; line-height: 26px; color: var(--ink); }
  .seal { position: absolute; left: 500px; top: 800px; width: 260px; height: 230px; }
  .signatures { position: absolute; left: 0; top: 995px; width: 850px; height: 110px; }
  .sig-area {
    position: absolute; top: 0; height: 70px; border-radius: 40px;
    background: radial-gradient(ellipse at 50% 50%, rgba(58,52,48,0.14) 0%, rgba(58,52,48,0) 70%);
  }
  .sig-area.first { left: 325px; width: 140px; }
  .sig-area.second { left: 480px; width: 170px; }
  .sig-label {
    position: absolute; top: 75px; left: 0; width: 350px; padding-right: 10px; text-align: right;
    font-weight: 600; font-size: 22px; color: var(--label);
  }
  .sig-name { position: absolute; top: 82px; font-size: 16px; color: var(--ink); }
  .sig-name.first { left: 350px; }
  .sig-name.second { left: 500px; }
  .page-number {
    position: absolute; left: 8px; top: 1170px;
    font-weight: 700; font-size: 22px; color: var(--title);
  }
</style>
</head>
<body>
<main class="certificate">
  <div class="emblem-backdrop" role="img" aria-label="Faint emblem decoration in the background"></div>
  <div class="wreath-backdrop" role="img" aria-label="Faint laurel wreath ornament behind the title"></div>

  <svg class="frame" width="850" height="1200" viewBox="0 0 850 1200" aria-hidden="true">
    <rect x="24" y="18" width="802" height="1138" fill="none" stroke="var(--gold)" stroke-width="2"/>
    <rect x="46" y="40" width="758" height="1094" fill="none" stroke="var(--gold-soft)" stroke-width="6" stroke-dasharray="2 3"/>
    <rect x="58" y="52" width="734" height="1070" fill="none" stroke="var(--gold)" stroke-width="1.5"/>
    <g fill="var(--gold)">
      <rect x="375" y="48" width="100" height="10"/>
      <rect x="375" y="1116" width="100" height="10"/>
      <path d="M425 40 l12 13 -12 13 -12 -13z"/>
      <path d="M425 1108 l12 13 -12 13 -12 -13z"/>
    </g>
  </svg>

  <h1 class="title">ZERTIFIKAT</h1>

  <svg class="ribbon" viewBox="0 0 530 130" aria-hidden="true">
    <defs>
      <path id="ribbon-curve" d="M60 92 Q265 20 470 92"/>
    </defs>
    <path d="M20 80 L60 70 L68 118 L30 124 L42 100z" fill="var(--gold-dark)"/>
    <path d="M510 80 L470 70 L462 118 L500 124 L488 100z" fill="var(--gold-dark)"/>
    <path d="M50 62 Q265 -8 480 62 L480 112 Q265 42 50 112z" fill="var(--gold)"/>
    <text class="ribbon-text" text-anchor="middle"><textPath href="#ribbon-curve" startOffset="50%">WACKER IM ALTER</textPath></text>
  </svg>

  <section class="details">
    <div class="row" style="top:10px"><span class="label">Zertifikat ID:</span><span class="value">7250441e9e</span></div>
    <div class="row" style="top:67px"><span class="label">Anbieter:</span><span class="value">Wacker im Alter<br>Ihr Zertifizierungsdienst</span></div>
    <div class="row" style="top:149px"><span class="label">Status:</span><span class="value">aktiv</span></div>
    <div class="row" style="top:206px"><span class="label">Unternehmen:</span><span class="value">Seniorendienst Lindenhof<br>Auenweg 7<br>12345 Stadt<br>Deutschland<br>kontakt@lindenhof-dienst.de</span></div>
    <div class="row" style="top:374px"><span class="label">Vertretungs-<br>berechtigter:</span><span class="value">Frau Greta<br>Lindner</span></div>
    <div class="row" style="top:473px"><span class="label">Erstprüfung am:</span><span class="value">07.04.2017</span></div>
    <div class="row" style="top:515px"><span class="label">gültig bis:</span><span class="value">07.04.2019</span></div>
  </section>

  <svg class="seal" viewBox="0 0 260 230" aria-label="Certificate seal" role="img">
    <path d="M150 130 L240 120 L250 200 L175 205z" fill="#e8e4dc" stroke="#bdb6aa" stroke-width="2"/>
    <circle cx="105" cy="115" r="90" fill="#c9c4bc"/>
    <circle cx="105" cy="115" r="60" fill="#f4f2ee"/>
  </svg>

  <section class="signatures">
    <div class="sig-area first" role="img" aria-label="Handwritten signature"></div>
    <div class="sig-area second" role="img" aria-label="Handwritten signature"></div>
    <span class="sig-label">Bestätigt von:</span>
    <span class="sig-name first">H. Brandt</span>
    <span class="sig-name second">C. Lehner</span>
  </section>

  <span class="page-number">24</span>
</main>
</body>
</html>
```